Marlow Vale Stud website

We would like to create a horse stud/agistment farm website similar to this websites we have attached below:
www.thornbeck.com.au
www.quillstead.com.au
www.brackley.com
www.pimsey.com.au
The main colour scheme are purple and white to align with the stable's racing colours.
We have also attach the company logo and also images of the farm and create some ideas for the website.
Many thanks for looking into this project!

```html
<!DOCTYPE html>
<html lang="en">
<head>
<meta charset="utf-8">
<title>Marlow Vale Stud</title>
<link href="https://fonts.googleapis.com/css2?family=Cinzel:wght@600;700&family=Raleway:wght@300;400;500;600;700;800&display=swap" rel="stylesheet">
<style>
:root{
  --purple:#3b1741;
  --purple-dark:#2f1034;
  --purple-line:#5a3660;
  --gold:#f6c31a;
  --white:#ffffff;
  --ink:#1c1c1c;
  --text:#555555;
  --muted:#9a9a9a;
  --panel:#f1f1ef;
  --band:#f4f4f4;
  --rule:#d6d6d6;
}
*{margin:0;padding:0;box-sizing:border-box}
html,body{width:1200px;height:2980px;overflow:hidden;background:var(--white)}
body{position:relative;font-family:'Raleway',sans-serif;color:var(--text)}
.abs{position:absolute}

/* header */
.site-header{left:0;top:0;width:1200px;height:136px;background:var(--purple)}
.brand{left:0;top:0;width:203px;height:136px;border-right:1px solid var(--purple-line);display:flex;align-items:center;justify-content:center;gap:8px}
.brand-name{color:var(--white);font-family:'Raleway',sans-serif;font-weight:700;font-size:17px;letter-spacing:1px;text-align:center;line-height:1.2}
.topbar{left:203px;top:0;width:797px;height:54px;border-bottom:1px solid var(--purple-line)}
.welcome{left:32px;top:20px;color:var(--white);font-size:11px;font-weight:600;letter-spacing:.5px}
.top-social{left:606px;top:12px;display:flex;gap:10px}
.top-social span{width:26px;height:26px;border-radius:50%;background:var(--purple-line);display:block}
.main-nav{left:203px;top:54px;width:797px;height:82px;display:flex;align-items:center;padding-left:32px;gap:38px}
.main-nav a{color:var(--white);text-decoration:none;font-size:14px;font-weight:500;letter-spacing:.5px}
.main-nav a.current{color:var(--gold)}
.search-cell{left:1000px;top:0;width:200px;height:136px;border-left:1px solid var(--purple-line)}
.search-cell svg{position:absolute;left:56px;top:60px}

/* hero */
.hero{left:0;top:136px;width:1200px;height:574px;background:linear-gradient(180deg,#4c5a3f 0%,#566846 35%,#5e5847 62%,#6e6255 100%)}
.hero-shade{left:0;top:136px;width:1200px;height:574px;background:rgba(0,0,0,.25)}
.hero-text{left:0;top:286px;width:1200px;text-align:center;color:var(--white)}
.hero-kicker{font-size:40px;font-weight:300}
.hero-title{font-size:60px;font-weight:800;line-height:64px;margin:18px auto 0;width:700px}
.hero-sub{font-size:15px;margin-top:26px}
.hero-pager{left:0;top:628px;width:1200px;text-align:center;font-size:14px;font-weight:700;font-style:italic;color:var(--white)}
.hero-pager span{margin:0 14px;text-decoration:underline}
.hero-pager .on{color:var(--gold)}

/* section headings */
.section-title{left:78px;width:1046px;display:flex;align-items:center;gap:22px;font-family:'Cinzel',serif;font-weight:700;font-size:34px;color:var(--ink);letter-spacing:1px}
.section-title::before,.section-title::after{content:"";flex:1;height:5px;border-top:1px solid var(--rule);border-bottom:1px solid var(--rule)}

/* stallions */
.stallion{top:845px;width:338px;height:307px}
.stallion .photo{width:100%;height:245px}
.stallion .name{height:62px;background:var(--purple);color:var(--white);font-size:17px;display:flex;align-items:center;justify-content:center;letter-spacing:.5px}
.arrow{top:946px;width:48px;height:48px;border-radius:50%;background:#777;border:3px solid var(--white);box-shadow:0 1px 4px rgba(0,0,0,.3);display:flex;align-items:center;justify-content:center}

/* news */
.news-card{top:1293px;width:512px;height:363px;background:var(--panel);display:flex}
.news-card .photo{width:272px;height:363px;flex:none}
.news-body{padding:48px 18px 0 18px;position:relative}
.tag{position:absolute;left:0;top:48px;background:var(--gold);color:#3b2c00;font-size:14px;padding:9px 24px;font-weight:500}
.news-title{margin-top:68px;font-size:17px;line-height:28px;color:#333}
.news-date{margin-top:14px;font-size:12px;color:#666;display:flex;align-items:center;gap:14px}
.news-date i{width:12px;height:12px;border:2px solid var(--gold);display:block}
.news-excerpt{margin-top:14px;font-size:12px;line-height:26px;color:#777}
.read-more{display:block;margin-top:10px;font-size:13px;font-style:italic;color:#555;text-decoration:underline}
.dots{left:0;top:1700px;width:1200px;display:flex;justify-content:center;gap:7px}
.dots span{width:12px;height:12px;border-radius:50%;border:1px solid #888}
.dots .on{background:var(--purple);border-color:var(--purple)}

/* video */
.video{left:78px;top:1856px;width:1046px;height:550px;background:linear-gradient(100deg,#5a4a3c 0%,#4a3a2e 35%,#3c2f2a 60%,#6d6660 100%)}
.play{left:543px;top:2097px;width:116px;height:80px}

/* newsletter */
.news-intro{left:270px;top:2540px;width:660px;text-align:center;font-size:13px;line-height:26px;color:var(--muted)}
.signup{left:282px;top:2628px;width:636px;height:58px;background:var(--white);box-shadow:0 2px 10px rgba(0,0,0,.18);display:flex;align-items:center;padding:0 6px 0 12px}
.signup svg{margin-right:14px}
.signup .field{flex:1;font-size:12px;color:#333}
.signup .subscribe{width:166px;height:48px;background:var(--purple);color:var(--white);font-size:17px;font-weight:600;display:flex;align-items:center;justify-content:center}

/* footer */
.contact-band{left:0;top:2752px;width:1200px;height:156px;background:var(--band)}
.contact-item{display:flex;align-items:center;gap:16px;font-size:15px;line-height:26px;color:#555}
.icon-circle{width:52px;height:52px;border-radius:50%;background:var(--white);border:1px solid #ccc;display:flex;align-items:center;justify-content:center;flex:none}
.foot-social{left:790px;top:2808px;display:flex;gap:10px}
.foot-social span{width:42px;height:42px;border-radius:50%;border:1px solid #999;background:var(--white);display:block}
.foot-social .on{background:var(--purple);border-color:var(--purple)}
.legal-bar{left:0;top:2908px;width:1200px;height:72px;background:var(--purple);color:var(--white);font-size:12px}
.copyright{left:82px;top:30px;font-weight:600}
.foot-links{right:76px;top:30px;display:flex;gap:8px}
.foot-links span.sep{opacity:.8}
</style>
</head>
<body>

<header class="site-header abs">
  <div class="brand abs"><span class="brand-name">MARLOW<br>VALE</span></div>
  <div class="topbar abs">
    <div class="welcome abs">WELCOME TO MARLOW VALE....!</div>
    <div class="top-social abs" aria-label="Social links"><span></span><span></span><span></span><span></span></div>
  </div>
  <nav class="main-nav abs">
    <a class="current" href="#">HOME</a><a href="#">STALLIONS</a><a href="#">NEWS</a><a href="#">SALES</a><a href="#">GALLERY</a><a href="#">ABOUT</a><a href="#">CONTACT</a>
  </nav>
  <div class="search-cell abs">
    <svg width="20" height="20" viewBox="0 0 20 20" fill="none" stroke="#ffffff" stroke-width="2"><circle cx="8" cy="8" r="6"/><line x1="12.5" y1="12.5" x2="18" y2="18"/></svg>
  </div>
</header>

<section>
  <div class="hero abs" role="img" aria-label="Rider jumping a horse over a show jumping fence"></div>
  <div class="hero-shade abs"></div>
  <div class="hero-text abs">
    <div class="hero-kicker">Just Ride With Us</div>
    <h1 class="hero-title">Our Horses Feed Your souls</h1>
    <p class="hero-sub">Horse Racing is waning in popularity</p>
  </div>
  <div class="hero-pager abs"><span>01</span><span class="on">02</span><span>03</span></div>
</section>

<section>
  <h2 class="section-title abs" style="top:766px">STALLIONS</h2>
  <div class="stallion abs" style="left:78px">
    <div class="photo" role="img" aria-label="Bay stallion standing on grass" style="background:linear-gradient(180deg,#3f6a2c,#5d8a35 70%,#6aa23c)"></div>
    <div class="name">HARBOUR GALE</div>
  </div>
  <div class="stallion abs" style="left:432px">
    <div class="photo" role="img" aria-label="Dark brown stallion in a paddock" style="background:linear-gradient(180deg,#5d7a3a,#6e8a48 65%,#7ea352)"></div>
    <div class="name">STILLWATERRUN</div>
  </div>
  <div class="stallion abs" style="left:788px">
    <div class="photo" role="img" aria-label="Chestnut stallion standing beside a hedge" style="background:linear-gradient(180deg,#5a8a3e,#4f7c36 55%,#b5b8b0)"></div>
    <div class="name">COPPER LANTERN</div>
  </div>
  <div class="arrow abs" style="left:52px"><svg width="10" height="12" viewBox="0 0 10 12"><path d="M8 1 2 6l6 5z" fill="#fff"/></svg></div>
  <div class="arrow abs" style="left:1100px"><svg width="10" height="12" viewBox="0 0 10 12"><path d="M2 1l6 5-6 5z" fill="#fff"/></svg></div>
</section>

<section>
  <h2 class="section-title abs" style="top:1218px">LATEST NEWS</h2>
  <article class="news-card abs" style="left:78px">
    <div class="photo" role="img" aria-label="Horse and rider clearing a jump" style="background:linear-gradient(180deg,#c7c9c4,#8a5a38 45%,#6b3d22)"></div>
    <div class="news-body">
      <span class="tag">Training</span>
      <h3 class="news-title">Lorem ipsum dolor sit incididunt ut labore.</h3>
      <div class="news-date"><i></i>7 March 2019</div>
      <p class="news-excerpt">Lorem ipsum dolor sit amet, consectetur adipiscing elit, sed do eiusmod tempor</p>
      <a class="read-more">Read More</a>
    </div>
  </article>
  <article class="news-card abs" style="left:614px">
    <div class="photo" role="img" aria-label="Two young riders with a horse at a fence" style="background:linear-gradient(180deg,#8c9b78,#6c7a5a 60%,#cfcfcb)"></div>
    <div class="news-body">
      <span class="tag">Training</span>
      <h3 class="news-title">Lorem ipsum dolor sit incididunt ut labore.</h3>
      <div class="news-date"><i></i>7 March 2019</div>
      <p class="news-excerpt">Lorem ipsum dolor sit amet, consectetur adipiscing elit, sed do eiusmod tempor</p>
      <a class="read-more">Read More</a>
    </div>
  </article>
  <div class="dots abs"><span></span><span class="on"></span><span></span></div>
</section>

<section>
  <h2 class="section-title abs" style="top:1778px">VEDIO</h2>
  <div class="video abs" role="img" aria-label="Video still of a woman in a hat fitting a bridle on a horse"></div>
  <svg class="play abs" viewBox="0 0 116 80" aria-label="Play video"><rect width="116" height="80" rx="20" fill="#3b1741"/><path d="M46 22l30 18-30 18z" fill="#fff"/></svg>
</section>

<section>
  <h2 class="section-title abs" style="top:2470px">NEWSLETTER</h2>
  <p class="news-intro abs">Lorem ipsum dolor sit amet, consectetur adipiscing elit, sed do eiusmod tempor incididunt ut labore et dolore magna aliqua. Ut enim ad minim veniam, quis nostrud exercitation.</p>
  <div class="signup abs">
    <svg width="20" height="14" viewBox="0 0 20 14"><rect width="20" height="14" rx="1" fill="#3b1741"/><path d="M1 1l9 7 9-7" fill="none" stroke="#fff" stroke-width="1.5"/></svg>
    <span class="field">Enter Email here.....</span>
    <span class="subscribe">SUBSCRIBE</span>
  </div>
</section>

<footer>
  <div class="contact-band abs">
    <div class="contact-item abs" style="left:78px;top:52px">
      <span class="icon-circle"><svg width="20" height="18" viewBox="0 0 20 18"><path d="M10 1 1 9h3v8h4v-5h4v5h4V9h3z" fill="#3b1741"/></svg></span>
      <span>418 Fernhill Road #6,<br>Linton, VT 05491</span>
    </div>
    <div class="contact-item abs" style="left:440px;top:52px">
      <span class="icon-circle"><svg width="18" height="18" viewBox="0 0 18 18"><path d="M4 1l3 4-2 2c1 2 3 4 5 5l2-2 4 3-2 3C8 16 2 10 1 4z" fill="#3b1741"/></svg></span>
      <span>555.019.2744<br>info@marlowvale.com</span>
    </div>
  </div>
  <div class="foot-social abs" aria-label="Social links"><span class="on"></span><span></span><span></span><span></span></div>
  <div class="legal-bar abs">
    <div class="copyright abs">© MARLOW VALE - 2019 . All Right Reserved</div>
    <div class="foot-links abs"><span>Home</span><span class="sep">|</span><span>Stallions</span><span class="sep">|</span><span>news</span><span class="sep">|</span><span>sales</span><span class="sep">|</span><span>Gallery</span><span class="sep">|</span><span>About</span><span class="sep">|</span><span>Contact</span></div>
  </div>
</footer>

</body>
</html>
```